Birchwell construction of ny Roofing flyer

We would like to create a flyer for roofing customers : commercial / real estate management / business / schools /warehouses

Flat roof specialists
Waterproofing experts

Special flat roof re layer @ 3.00 per sq ft

Roof leak repairs
Flashing
Waterproofing

Call 555 2419630

For pictures find torch down roof applications
Flat roofs ny

```html
<!DOCTYPE html>
<html lang="en">
<head>
<meta charset="utf-8">
<title>Birchwell construction of ny – Roofing flyer</title>
<link rel="stylesheet" href="https://fonts.googleapis.com/css2?family=Russo+One&family=Bebas+Neue&family=Oswald:wght@300;400;500&family=Montserrat:wght@500;700&display=swap">
<style>
  :root{
    --page:#e9e6e1;
    --green-top:#12331f;
    --green-mid:#0f2c1a;
    --green-deep:#081a0f;
    --orange:#f26f12;
    --orange-bright:#ff7a16;
    --white:#ffffff;
    --ink:#1b1b1b;
    --line:#c9c9c9;
  }
  *{margin:0;padding:0;box-sizing:border-box}
  html,body{width:1200px;height:1200px;overflow:hidden;background:var(--page)}
  .flyer{
    position:absolute;left:200px;top:35px;width:800px;height:1130px;overflow:hidden;
    background:linear-gradient(180deg,var(--green-top) 0%,var(--green-mid) 55%,var(--green-deep) 100%);
    box-shadow:0 6px 24px rgba(0,0,0,.25);
  }
  .hero-photo{
    position:absolute;left:0;top:0;width:800px;height:372px;
    background:
      radial-gradient(ellipse 45% 12% at 50% 92%,rgba(255,150,40,.95),rgba(255,110,20,.5) 45%,transparent 75%),
      linear-gradient(90deg,#8d8b88 0%,#9b8f86 30%,#5d5c5e 55%,#2c2f38 75%,#4d4f56 100%);
  }
  .hero-photo::after{
    content:"";position:absolute;left:0;right:0;bottom:0;height:60px;
    background:linear-gradient(180deg,transparent,var(--green-top));
  }
  .brand{
    position:absolute;left:44px;top:440px;width:210px;
    display:flex;align-items:center;gap:10px;
    font-family:"Russo One",sans-serif;color:var(--white);
    font-size:22px;line-height:1.15;text-transform:uppercase;
  }
  .brand-mark{width:16px;height:16px;background:var(--white);flex:none}
  .headline{
    position:absolute;left:313px;top:380px;white-space:nowrap;
    font-family:"Russo One",sans-serif;color:var(--white);font-weight:400;
    font-size:58px;line-height:68px;letter-spacing:1px;
  }
  .brush{
    position:absolute;background:var(--orange);white-space:nowrap;
    clip-path:polygon(2% 18%,8% 6%,40% 10%,70% 2%,97% 8%,100% 30%,98% 70%,94% 96%,60% 88%,30% 98%,5% 90%,0% 60%);
    display:flex;align-items:center;justify-content:center;
    font-family:"Bebas Neue",sans-serif;color:var(--white);
  }
  .brush-tagline{left:282px;top:530px;width:466px;height:60px;font-size:46px;letter-spacing:.5px}
  .brush-all{left:485px;top:837px;width:187px;height:56px;font-size:38px}
  .brush-call{left:19px;top:1050px;width:395px;height:62px;font-size:32px;color:var(--ink);justify-content:flex-start;padding-left:34px}
  .offer{
    position:absolute;left:317px;top:610px;width:423px;height:106px;
    border:1.5px dashed var(--line);border-radius:14px;
    display:flex;align-items:center;padding-left:24px;gap:8px;white-space:nowrap;
  }
  .offer-price{font-family:"Oswald",sans-serif;font-weight:500;color:var(--orange-bright);font-size:60px;line-height:1;white-space:nowrap}
  .offer-unit{
    background:var(--orange);color:var(--ink);font-family:"Oswald",sans-serif;font-weight:500;
    font-size:10px;writing-mode:vertical-rl;transform:rotate(180deg);padding:3px 2px;height:56px;text-align:center;
  }
  .offer-label{font-family:"Oswald",sans-serif;font-weight:300;color:var(--white);font-size:27px;line-height:1.15;margin-left:6px;white-space:nowrap}
  .audience{position:absolute;list-style:none;font-family:"Montserrat",sans-serif;font-weight:500;color:var(--white);font-size:18px;line-height:24px}
  .audience-left{left:317px;top:735px}
  .audience-right{left:580px;top:730px}
  .audience li{display:flex;align-items:flex-start;gap:6px;white-space:nowrap}
  .audience svg{margin-top:5px;flex:none}
  .photo{position:absolute;border:2px solid var(--white);border-radius:12px;overflow:hidden}
  .photo-torch{left:48px;top:667px;width:186px;height:164px;background:radial-gradient(ellipse 40% 25% at 55% 62%,#ffb03a,#d2651a 45%,#3b2a1c 80%)}
  .photo-roof{left:53px;top:850px;width:185px;height:165px;background:linear-gradient(180deg,#8a7f78 0%,#b9bec4 30%,#dfe2e5 100%)}
  .photo-crew{left:265px;top:845px;width:185px;height:165px;background:linear-gradient(160deg,#3f5b2c 0%,#6f7d55 45%,#b0a596 100%)}
  .services{position:absolute;left:485px;top:918px;width:285px;display:flex}
  .service{flex:1;display:flex;flex-direction:column;align-items:center;gap:6px;
    font-family:"Oswald",sans-serif;font-weight:400;color:var(--white);font-size:15px;line-height:1.2;text-align:center;text-transform:uppercase}
  .service + .service{border-left:1px solid var(--orange)}
  .website{position:absolute;left:455px;top:1062px;white-space:nowrap;font-family:"Montserrat",sans-serif;font-weight:500;color:var(--white);font-size:28px;letter-spacing:.5px}
  .website b{font-weight:700}
</style>
</head>
<body>
<main class="flyer">
  <div class="hero-photo" role="img" aria-label="Roofers applying torch-down membrane on a flat roof, flame at the seam"></div>

  <div class="brand"><span class="brand-mark"></span><span>Birchwell construction of ny</span></div>

  <h1 class="headline">FLAT ROOF<br>SPECIALISTS</h1>
  <div class="brush brush-tagline">WATERPROOFING EXPERTS</div>

  <div class="offer">
    <span class="offer-price">@ 3.00</span>
    <span class="offer-unit">PER SQ FT</span>
    <span class="offer-label">SPECIAL FLAT<br>ROOF RE LAYER</span>
  </div>

  <div class="photo photo-torch" role="img" aria-label="Close-up of a torch flame sealing roofing membrane"></div>

  <ul class="audience audience-left">
    <li><svg width="14" height="14" viewBox="0 0 14 14"><rect x="1" y="1" width="12" height="12" fill="none" stroke="#f26f12" stroke-width="1.5"/><path d="M3.5 7l2.5 2.5 5-6" fill="none" stroke="#f26f12" stroke-width="1.8"/></svg>Commercial</li>
    <li><svg width="14" height="14" viewBox="0 0 14 14"><rect x="1" y="1" width="12" height="12" fill="none" stroke="#f26f12" stroke-width="1.5"/><path d="M3.5 7l2.5 2.5 5-6" fill="none" stroke="#f26f12" stroke-width="1.8"/></svg><span>Real estate<br>management</span></li>
  </ul>
  <ul class="audience audience-right">
    <li><svg width="14" height="14" viewBox="0 0 14 14"><rect x="1" y="1" width="12" height="12" fill="none" stroke="#f26f12" stroke-width="1.5"/><path d="M3.5 7l2.5 2.5 5-6" fill="none" stroke="#f26f12" stroke-width="1.8"/></svg>Business</li>
    <li><svg width="14" height="14" viewBox="0 0 14 14"><rect x="1" y="1" width="12" height="12" fill="none" stroke="#f26f12" stroke-width="1.5"/><path d="M3.5 7l2.5 2.5 5-6" fill="none" stroke="#f26f12" stroke-width="1.8"/></svg>Schools</li>
    <li><svg width="14" height="14" viewBox="0 0 14 14"><rect x="1" y="1" width="12" height="12" fill="none" stroke="#f26f12" stroke-width="1.5"/><path d="M3.5 7l2.5 2.5 5-6" fill="none" stroke="#f26f12" stroke-width="1.8"/></svg>Warehouses</li>
  </ul>

  <div class="photo photo-roof" role="img" aria-label="Finished white flat roof with vents and city buildings behind"></div>
  <div class="photo photo-crew" role="img" aria-label="Roofer kneeling on a roof torching new membrane"></div>

  <div class="brush brush-all">WE DO IT ALL</div>

  <div class="services">
    <div class="service">
      <svg width="44" height="34" viewBox="0 0 44 34"><path d="M4 20L22 4l18 16" fill="none" stroke="#fff" stroke-width="4"/><path d="M11 18v12h22V18" fill="none" stroke="#fff" stroke-width="2.5"/><path d="M19 28c-2-4 2-6 2-10 3 3 5 6 3 10z" fill="#fff"/></svg>
      <span>Roof<br>leak repairs</span>
    </div>
    <div class="service">
      <svg width="44" height="34" viewBox="0 0 44 34"><path d="M4 24L22 8l18 16" fill="none" stroke="#fff" stroke-width="5"/></svg>
      <span>Flashing</span>
    </div>
    <div class="service">
      <svg width="44" height="34" viewBox="0 0 44 34"><path d="M16 2c-4 7-8 11-8 16a8 8 0 0016 0c0-5-4-9-8-16z" fill="#fff"/><path d="M24 28c6 0 10-3 12-8" fill="none" stroke="#fff" stroke-width="3"/><path d="M31 18l6 1 1-6" fill="none" stroke="#fff" stroke-width="3"/></svg>
      <span>Water<br>proofing</span>
    </div>
  </div>

  <div class="brush brush-call">CALL US TODAY- 555 2419630</div>
  <div class="website">www.<b>birchwellny</b>.com</div>
</main>
</body>
</html>
```